Local Chiropractoc needs Modern Website

This website needs to have an upscale look with a very modern feel.

This is for a home page psd layout and an interior page psd file so 2 files total

Below is the information and websites to reference

Add Logo that is attached.

Build a color scheme similar to this website image titled "chiro-1" using the golds, whites, blacks and browns from the color of the logo

I want to see a light background so it makes the images and logo stick out

Must Include these pages in a horizontal menu bar in this order:
Home, Why Fair Ridge?, How Chiropractic Helps, Ask the Doctor, Work Place Wellness, Request an Appointment, Blog, Contact Us

Please add the following social media logos to the top and footer of the website: Chatterly, Plexo+, Vidzio

Build a "classy looking" Make An Appointment Button into the header with the contact info below

Phone Number:
555-014-2297

Address:
4172 North Maple Blvd, Suite #7
Harlow Springs, FL 34990

This website needs 4 rotating banners. Please reference a layout similar to this for the banners: http://hollowpinespine.com/. However design it nicer than this website

Below are the description for each banner

Rotating Banner #1
Use Image: Patients are Saying
Add a line of text: "What our Patients are Saying"

Rotating Banner #2
Use Image: Becoming a Patient
Add a line of text: "Interested in Becoming a Patient"

Rotating Banner #3
Use Image: Dinner with Doctor
Add a line of text: "Win A free Dinner with Dr. Hollins"

Rotating Banner #4
Use Image: Chatterly
Add a line of text: Follow us on Chatterly
Bullet point these 4 lines underneath the "Follow us on Chatterly" text:
- Cutting Edge Health News
- Healthy Recipes
- Newest Health Products
- Clinic Events

I'd like to see a free consultation box similar to the "chiro-1" image. Fields to include are: First Name, Last Name, Phone Number, Comments

For the body, please fill it with latin text. Please design a professional 2 column layout similar to the www.hollowpinespine.com website. (DO NOT COPY THIS WEBSITE, USE IT AS REFERENCE)

In the left column include in this order:
Video
Rate us on Plexo Button, Find us on Chatterly Button
Welcome Letter

In the right column include this:

Office Hours
Monday: 8:00-11:00, 2:00-5:00
Tuesday: 8:30-11:00, 2:00-5:30
Wednesday: 8:00-11:00, 2:00-5:00
Thursday: 10:00-12:00, 2:30-5:00
Friday: 8:00-10:00, 1:00-5:00
Saturday: Closed
Sunday: Closed

Patient Testimonials
Fill with a latin text testimonial. This spot will rotate different testimonials

For the footer please design something similar to the layout of this: http://www.tidewellhealer.com/

Also include in the Footer: Powered by Crestline Pixel Group

```html
<!DOCTYPE html>
<html lang="en">
<head>
<meta charset="utf-8">
<title>Fair Ridge Chiropractic</title>
<link rel="stylesheet" href="https://fonts.googleapis.com/css2?family=Open+Sans:ital,wght@0,400;0,600;0,700;1,400&family=Ubuntu:wght@400;500;700&display=swap">
<style>
:root{
  --gold:#b8995a;
  --gold-dark:#9e7f43;
  --gold-light:#d9c59a;
  --ink:#2b2b2b;
  --paper:#f1eee8;
  --white:#ffffff;
  --text:#6b6b6b;
  --rule:#e6e2da;
  --row:#f4f3f1;
}
*{box-sizing:border-box;margin:0;padding:0}
html,body{width:912px;height:1200px;overflow:hidden}
body{background:var(--paper);font-family:"Open Sans",sans-serif;color:var(--text);position:relative}
.abs{position:absolute}

/* header */
.brand{left:122px;top:66px;display:flex;align-items:center;gap:8px}
.brand-mark{width:16px;height:16px;background:var(--ink)}
.brand-name{font-family:"Ubuntu",sans-serif;font-weight:700;font-size:20px;line-height:1.1;color:var(--ink);text-transform:uppercase;letter-spacing:.3px}
.top-social{right:106px;top:58px;display:flex;gap:5px}
.top-social a{font-size:8px;font-weight:600;color:var(--gold-dark);border:1px solid var(--gold);border-radius:9px;padding:3px 7px;text-decoration:none}
.contact-bar{left:393px;top:88px;width:290px;height:35px;background:var(--ink);display:flex;align-items:center;color:var(--white);white-space:nowrap}
.contact-item{display:flex;align-items:center;gap:7px;padding:0 9px;height:100%}
.contact-item+.contact-item{border-left:1px solid #444}
.contact-item b{display:block;font-size:7.5px;font-weight:700}
.contact-item i{display:block;font-size:6.5px;color:#9a9a9a}
.appt-btn{left:676px;top:88px;width:130px;height:35px;background:var(--gold);color:var(--white);font-size:7.5px;font-weight:700;display:flex;align-items:center;justify-content:center;text-transform:uppercase;white-space:nowrap;clip-path:polygon(10px 0,100% 0,100% 100%,10px 100%,0 50%)}
.main-nav{left:105px;top:137px;width:701px;height:46px;background:var(--ink);display:flex;font-size:6.8px;font-weight:600;text-transform:uppercase;white-space:nowrap}
.main-nav a{color:var(--white);text-decoration:none;display:flex;align-items:center;justify-content:center;flex:auto;padding:0 6px;border-right:1px solid #3d3d3d}
.main-nav a:last-child{border:none}
.main-nav a.active{background:var(--gold)}

/* banner */
.banner{left:105px;top:195px;width:701px;height:227px;overflow:hidden}
.banner-photo{left:155px;top:0;width:440px;height:227px;background:linear-gradient(120deg,#3d5a6e,#b89574 45%,#e4cdb4 70%,#d8d2c8)}
.consult{left:0;top:0;width:155px;height:227px;background:linear-gradient(#6b5d4c,#4a4037);padding:8px 12px;color:var(--white)}
.consult small{font-size:7px;text-transform:uppercase;display:block;padding-left:12px}
.consult h3{font-size:10px;font-weight:700;text-transform:uppercase;padding-left:12px;margin-bottom:16px}
.consult h4{font-size:7px;font-style:italic;font-weight:600;text-transform:uppercase;text-align:center;margin-bottom:8px}
.field{height:19px;border:1px solid rgba(255,255,255,.7);border-radius:2px;font-size:7px;font-style:italic;padding:4px 10px;margin-bottom:5px}
.field.tall{height:45px}
.submit{display:inline-block;background:var(--gold);font-size:7px;font-weight:700;padding:6px 12px;border-radius:2px;margin-top:2px}
.slide-panel{left:0;top:0;width:701px;height:227px}
.slide-copy{left:513px;top:42px;width:170px;color:var(--white)}
.slide-copy h2{font-family:"Ubuntu",sans-serif;font-weight:500;font-size:15px;line-height:1.4;margin-bottom:8px}
.slide-copy p{font-size:7.5px;line-height:1.95;margin-bottom:12px}
.readmore{display:inline-block;background:var(--white);color:var(--ink);font-size:7px;padding:7px 11px;border-radius:2px}
.dots{left:513px;top:208px;display:flex;gap:4px}
.dots span{width:6px;height:6px;border-radius:50%;background:rgba(255,255,255,.45)}
.dots span.on{background:var(--white)}

/* content */
.content{left:105px;top:433px;width:701px;height:652px;background:var(--white);border-radius:3px}
.section-title{font-family:"Ubuntu",sans-serif;font-size:10px;font-weight:500;text-transform:uppercase;color:var(--ink);display:flex;align-items:center;gap:6px}
.section-title::before{content:"";width:2px;height:9px;background:var(--gold)}
.section-title::after{content:"";flex:1;height:6px;background:#f3f1ed}
.video{left:18px;top:60px;width:439px;height:227px;border:1px solid var(--rule);padding:6px}
.video-photo{width:100%;height:192px;background:linear-gradient(160deg,#cfd6c7,#a8b990 50%,#6f8b4c)}
.video-bar{height:22px;background:var(--ink);display:flex;align-items:center;gap:8px;padding:0 8px;font-size:6px;color:#999}
.video-track{flex:1;height:2px;background:#555;position:relative}
.video-track span{position:absolute;left:0;top:0;width:29%;height:2px;background:var(--gold-light)}
.play{left:202px;top:97px;width:28px;height:28px;background:rgba(255,255,255,.6);border-radius:3px}
.social-btn{top:340px;width:210px;height:46px;background:var(--ink);display:flex;border-bottom:2px solid var(--gold)}
.social-btn .sq{width:46px;background:var(--gold)}
.social-btn div{padding:9px 0 0 16px;color:var(--white)}
.social-btn small{display:block;font-size:6.5px;font-weight:600;text-transform:uppercase}
.social-btn strong{font-family:"Ubuntu",sans-serif;font-size:20px;font-weight:500;color:var(--gold);text-transform:uppercase;line-height:1.1}
.hours{left:474px;top:35px;width:210px;border:1px solid var(--rule)}
.hours h3{height:33px;background:var(--gold);color:var(--white);font-family:"Ubuntu",sans-serif;font-size:10px;font-weight:500;text-transform:uppercase;display:flex;align-items:center;justify-content:center}
.hours table{width:100%;border-collapse:collapse;font-size:6.8px}
.hours td{height:22.7px;padding:0 11px}
.hours tr:nth-child(odd){background:var(--row)}
.hours td:first-child{color:var(--ink);font-weight:600}
.hours td:last-child{text-align:right;color:#888}
.hours tr.closed td{color:var(--gold)}
.testimonial{left:474px;top:283px;width:210px;height:103px;background:#f3f2f0}
.testimonial p{font-size:7px;font-style:italic;line-height:2.15;color:#8a8a8a;padding:14px 20px 0 20px}
.testimonial footer{position:absolute;left:0;bottom:0;width:100%;height:22px;background:var(--gold);color:var(--white);font-size:6.5px;font-weight:700;display:flex;align-items:center;justify-content:space-between;padding:0 16px}
.tdots{display:flex;gap:3px}
.tdots span{width:6px;height:6px;border-radius:50%;background:rgba(255,255,255,.5)}
.tdots span.on{background:var(--white)}
.divider{left:0;top:421px;width:701px;height:1px;background:#efede9}
.letter{left:18px;top:482px;width:328px;font-size:7.5px;line-height:2.02;text-align:justify;color:#777}
.letter-photo{left:360px;top:479px;width:324px;height:140px;background:linear-gradient(110deg,#c7d6a4,#e0b8a8 40%,#d9c3a6 70%,#9cb571)}

/* footer */
.footer-links{left:0;top:1086px;width:912px;height:57px;background:var(--gold)}
.footer-links nav{position:absolute;left:122px;top:23px;font-size:7.5px;font-weight:600;color:var(--white);white-space:nowrap}
.footer-links nav a{color:var(--white);text-decoration:none}
.footer-links nav span{margin:0 4px}
.footer-brand{position:absolute;right:122px;top:17px;display:flex;align-items:center;gap:5px;font-family:"Ubuntu",sans-serif;font-weight:700;font-size:10px;line-height:1.1;color:var(--white);text-transform:uppercase}
.footer-brand .mk{width:8px;height:8px;background:var(--white)}
.footer-base{left:0;top:1143px;width:912px;height:57px;background:var(--ink);color:var(--white);font-size:7.5px;font-weight:700}
.footer-addr{position:absolute;left:122px;top:20px;line-height:1.5}
.footer-addr i{font-weight:400;display:block;padding-left:28px}
.footer-social{position:absolute;left:50%;top:16px;transform:translateX(-50%);display:flex;gap:6px}
.footer-social a{font-size:7px;font-weight:600;color:var(--gold-light);border:1px solid var(--gold);border-radius:2px;padding:5px 6px;text-decoration:none}
.footer-copy{position:absolute;right:122px;top:20px;text-align:right;line-height:1.5}
.footer-copy i{font-weight:400}
.footer-copy em{color:var(--gold);font-weight:400}
</style>
</head>
<body>

<header>
  <div class="abs brand">
    <span class="brand-mark"></span>
    <span class="brand-name">Fair Ridge<br>Chiropractic</span>
  </div>
  <div class="abs top-social">
    <a href="#">Chatterly</a><a href="#">Plexo+</a><a href="#">Vidzio</a>
  </div>
  <div class="abs contact-bar">
    <div class="contact-item">
      <svg width="14" height="14" viewBox="0 0 24 24"><path fill="#b8995a" d="M6.6 10.8a15 15 0 0 0 6.6 6.6l2.2-2.2c.3-.3.7-.4 1-.2 1.1.4 2.3.6 3.6.6.6 0 1 .4 1 1V20c0 .6-.4 1-1 1A17 17 0 0 1 3 4c0-.6.4-1 1-1h3.5c.6 0 1 .4 1 1 0 1.3.2 2.5.6 3.6.1.3 0 .7-.2 1z"/></svg>
      <div><b>555-014-2297</b><i>info@fairridge.example</i></div>
    </div>
    <div class="contact-item">
      <svg width="15" height="14" viewBox="0 0 24 22"><path fill="#b8995a" d="M12 1 1 11h3v10h6v-6h4v6h6V11h3z"/></svg>
      <div><b>4172 North Maple Blvd, Suite #7</b><i>Harlow Springs, FL 34990</i></div>
    </div>
  </div>
  <a class="abs appt-btn">Make an Appointment</a>
  <nav class="abs main-nav">
    <a>Home</a><a class="active">Why Fair Ridge?</a><a>How Chiropractic Helps</a><a>Ask the Doctor</a><a>Work Place Wellness</a><a>Request an Appointment</a><a>Blog</a><a>Contact Us</a>
  </nav>
</header>

<section class="abs banner">
  <div class="abs banner-photo" role="img" aria-label="Photo of a smiling couple sharing dinner with the doctor"></div>
  <svg class="abs slide-panel" viewBox="0 0 701 227" aria-hidden="true"><path fill="#b8995a" d="M461 0H701V227H490C560 160 500 110 555 60 575 35 540 15 461 0Z"/></svg>
  <form class="abs consult">
    <small>Contact us now &amp; get your</small>
    <h3>Free Consultation</h3>
    <h4>Wellness begins here</h4>
    <div class="field">First Name</div>
    <div class="field">Last Name</div>
    <div class="field">Phone Number</div>
    <div class="field tall">Comments ...</div>
    <span class="submit">Submit ➜</span>
  </form>
  <div class="abs slide-copy">
    <h2>Win a Free Dinner<br>With Dr. Hollins</h2>
    <p>Proin sit amet venenatis ante. Nulla lorem felis, maximus tincidunt felis nec, mattis con dimentum enim. Maecenas non sodales nund.</p>
    <span class="readmore">Read More</span>
  </div>
  <div class="abs dots"><span></span><span class="on"></span><span></span><span></span></div>
</section>

<main class="abs content">
  <h2 class="abs section-title" style="left:18px;top:38px;width:439px">Our Videos</h2>
  <div class="abs video">
    <div class="video-photo" role="img" aria-label="Video still of a multi-generation family picnicking outdoors"></div>
    <div class="video-bar"><span>▶</span><span>00:28</span><div class="video-track"><span></span></div><span>02:36</span></div>
    <div class="abs play"><svg width="28" height="28"><path d="M12 9l7 5-7 5z" fill="#555"/></svg></div>
  </div>

  <h2 class="abs section-title" style="left:18px;top:315px;width:439px">We're on Social Medias</h2>
  <a class="abs social-btn" style="left:18px"><span class="sq"></span><div><small>Rate us on</small><strong>Plexo</strong></div></a>
  <a class="abs social-btn" style="left:247px"><span class="sq"></span><div><small>Find us on</small><strong>Chatterly</strong></div></a>

  <aside class="abs hours">
    <h3>Office Hours</h3>
    <table>
      <tr><td>Monday</td><td>8:00-11:00 AM, 2:00-5:00 PM</td></tr>
      <tr><td>Tuesday</td><td>8:30-11:00 AM, 2:00-5:30 PM</td></tr>
      <tr><td>Wednesday</td><td>8:00-11:00 AM, 2:00-5:00 PM</td></tr>
      <tr><td>Thursday</td><td>10:00-12:00 AM, 2:30-5:00 PM</td></tr>
      <tr><td>Friday</td><td>8:00-10:00 AM, 1:00-5:00 PM</td></tr>
      <tr class="closed"><td>Saturday</td><td>Closed</td></tr>
      <tr class="closed"><td>Sunday</td><td>Closed</td></tr>
    </table>
  </aside>

  <h2 class="abs section-title" style="left:474px;top:261px;width:210px">Patient Testimonials</h2>
  <blockquote class="abs testimonial">
    <p>Pellentesque habitant morbi tristique senectus et netus et malesuada fames ac turpis egestas. Donec faucibus aliquet dui, nec congue orci sagittis eget.</p>
    <footer><span>- Mr. Daniel Prescott -</span><span class="tdots"><span></span><span class="on"></span><span></span><span></span></span></footer>
  </blockquote>

  <div class="abs divider"></div>

  <h2 class="abs section-title" style="left:18px;top:459px;width:666px">Welcome Letter</h2>
  <div class="abs letter">
    <p>Hello Dear Visitor,<br>Vestibulum malesuada tortor volutpat risus finibus, in consequat nibh dictum. Pellentesque vestibulum nisi nisl, vel accumsan dui consequat sed. Integer non justo et mi interdum pretium. Proin ut pulvinar eros. Pellentesque at luctus odio, a ullamcorper urna. Nam semper feugiat massa non pulvinar. Curabitur sagittis, odio eget posuere ultricies, sem nisi pulvinar turpis, at laoreet arcu neque lacinia odio. Nulla nec nunc ac felis auctor fermentum quis ut justo. Donec ultricies feugiat accumsan. Integer leo justo, dapibus id mauris quis, vestibulum rutrum arcu. Etiam sed ipsum eu augue condimentum ullamcorper vel ac sapien. Cras sed lorem et est interdum commodo vitae sit amet orci. Ut mattis tempor metus sed venenatis.</p>
  </div>
  <div class="abs letter-photo" role="img" aria-label="Photo of a happy family of four hugging outdoors"></div>
</main>

<footer>
  <div class="abs footer-links">
    <nav><a>Home</a><span>|</span><a>Why Fair Ridge?</a><span>|</span><a>How Chiropractic Helps</a><span>|</span><a>Ask the Doctor</a><span>|</span><a>Work Place Wellness</a><span>|</span><a>Request an Appointment</a><span>|</span><a>Blog</a><span>|</span><a>Contact Us</a></nav>
    <div class="footer-brand"><span class="mk"></span><span>Fair Ridge<br>Chiropractic</span></div>
  </div>
  <div class="abs footer-base">
    <div class="footer-addr">4172 North Maple Blvd, Suite #7<i>Harlow Springs, FL 34990</i></div>
    <div class="footer-social"><a href="#">Chatterly</a><a href="#">Plexo+</a><a href="#">Vidzio</a></div>
    <div class="footer-copy">Copyright © 2015, Fair Ridge Chiropractic<br><i>Powered by <em>Crestline Pixel Group</em></i></div>
  </div>
</footer>

</body>
</html>
```